Business cards for Harbourline Supply Pty Ltd that import building products into Australia from China
Target Market(s)
Business to Business
Industry/Entity Type
Business
Contact Information for Business Card
Front: Logo and Business Name
Rear:
Desmond Varrick
General Manager
Mobile: 0427 561 394
email: dessie@harbourlinesupply.com.au
alternative email: dessie@outbackworks.com.au
web: www.harbourlinesupply.com.au
Adelaide, Brisbane and Darwin
Colors
ec1f27
fbee3d

```html
<!DOCTYPE html>
<html lang="en">
<head>
<meta charset="utf-8">
<title>Harbourline Supply Pty Ltd – Business Cards</title>
<link rel="stylesheet" href="https://fonts.googleapis.com/css2?family=Open+Sans:wght@400;700&family=Oswald:wght@500&display=swap">
<style>
  :root {
    --brand-red: #ec1f27;
    --brand-yellow: #fbee3d;
    --yellow-shade: #e0d331;
    --card-black: #161616;
    --text-white: #ffffff;
    --text-light: #dcdcdc;
    --page-bg: #d9d9d9;
  }
  html, body {
    margin: 0;
    width: 1200px;
    height: 1000px;
    overflow: hidden;
    background: var(--page-bg);
  }
  .sheet {
    position: relative;
    width: 1200px;
    height: 1000px;
  }
  .card {
    position: absolute;
    left: 250px;
    width: 700px;
    height: 400px;
    border-radius: 18px;
    overflow: hidden;
    box-shadow: 0 6px 18px rgba(0,0,0,0.25);
  }
  .card svg { display: block; width: 700px; height: 400px; }
  .card--front { top: 70px; }
  .card--back { top: 530px; }
  .company-name {
    font-family: "Open Sans", sans-serif;
    font-weight: 700;
    fill: var(--text-white);
    letter-spacing: 0.5px;
  }
  .holder-name {
    font-family: "Oswald", sans-serif;
    font-weight: 500;
    fill: var(--text-white);
    letter-spacing: 1px;
  }
  .holder-title {
    font-family: "Open Sans", sans-serif;
    font-weight: 400;
    fill: var(--brand-red);
    letter-spacing: 0.5px;
  }
  .contact-line {
    font-family: "Open Sans", sans-serif;
    font-weight: 400;
    fill: var(--text-light);
  }
  .contact-highlight { fill: var(--brand-yellow); }
  .contact-icon { fill: var(--brand-yellow); }
  .contact-icon-stroke { fill: none; stroke: var(--brand-yellow); stroke-width: 1.2; }
</style>
</head>
<body>
<main class="sheet">

  <section class="card card--front" aria-label="Card front">
    <svg viewBox="0 0 700 400" xmlns="http://www.w3.org/2000/svg">
      <rect class="card-base" width="700" height="400" fill="var(--card-black)"/>
      <rect class="brand-square" x="336" y="140" width="28" height="28" fill="var(--brand-red)"/>
      <text class="company-name" x="350" y="220" font-size="30" text-anchor="middle">HARBOURLINE SUPPLY PTY LTD</text>
    </svg>
  </section>

  <section class="card card--back" aria-label="Card back">
    <svg viewBox="0 0 700 400" xmlns="http://www.w3.org/2000/svg">
      <rect class="card-base" width="700" height="400" fill="var(--card-black)"/>

      <path class="wave wave--top-yellow" d="M300,0 H700 V232 C580,232 520,150 420,95 C360,62 330,30 300,0 Z" fill="var(--brand-yellow)"/>
      <path class="wave wave--top-yellow-shade" d="M460,120 C540,175 600,205 700,210 V232 C590,232 530,180 460,120 Z" fill="var(--yellow-shade)"/>
      <path class="wave wave--top-red" d="M0,0 H430 C300,20 160,45 0,62 Z" fill="var(--brand-red)"/>

      <path class="wave wave--bottom-yellow" d="M0,318 C160,300 340,320 480,400 H0 Z" fill="var(--brand-yellow)"/>
      <path class="wave wave--bottom-yellow-shade" d="M140,380 C250,360 360,370 440,400 H140 Z" fill="var(--yellow-shade)"/>
      <path class="wave wave--bottom-red" d="M430,400 C520,355 610,340 700,338 V400 Z" fill="var(--brand-red)"/>

      <text class="holder-name" x="45" y="118" font-size="32">DESMOND VARRICK</text>
      <text class="holder-title" x="45" y="142" font-size="16">General Manager</text>

      <g class="contact-list">
        <path class="contact-icon" d="M47,202 l3,-2 2,4 -2,1.5 c1,2 2.5,3.5 4.5,4.5 l1.5,-2 4,2 -2,3 c-6,0 -11,-5 -11,-11 z"/>
        <text class="contact-line" x="70" y="213" font-size="15">0427 561 394</text>

        <rect class="contact-icon" x="46" y="228" width="14" height="10" rx="1"/>
        <polyline points="46,228 53,234 60,228" stroke="var(--card-black)" stroke-width="1.2" fill="none"/>
        <text class="contact-line" x="70" y="238" font-size="15">dessie@harbourlinesupply.com.au</text>

        <circle class="contact-icon" cx="53" cy="258" r="7"/>
        <path class="contact-icon-stroke" d="M46,258 H60 M53,251 V265 M48,254 H58 M48,262 H58" stroke="var(--card-black)" style="stroke: var(--card-black)"/>
        <text class="contact-line" x="70" y="263" font-size="15">www.<tspan class="contact-highlight">harbourlinesupply</tspan>.com.au</text>
      </g>

      <rect class="brand-square" x="598" y="228" width="22" height="22" fill="var(--brand-red)"/>
      <text class="company-name" x="655" y="292" font-size="21" text-anchor="end">HARBOURLINE SUPPLY PTY LTD</text>
    </svg>
  </section>

</main>
</body>
</html>
```